Cutting Edge Property Services Provider is Looking to Update Business Card Design

We are looking to freshen up our business cards to match our cutting edge technology based image.

KORVANEX - Where Care Finds Its Pulse

More information about our company can be found on our website at www.korvanex-demo.net

We integrate technology in a historically low tech industry.

We have appeared on the Brisk 300/3000 list 2 years in a row and we're previously recognized as the 5th Quickest Rising Firm in San Diego.

Our core colors are blue and white, but are not against accents that might improve our image.

We currently have our Mission Statement on our Business Cards in a folding design:
KORVANEX IS THE LEADING BUILDING SERVICES INNOVATOR. BY COMBINING TECHNOLOGY WITH FUNCTIONAL TOOS THAT IMPROVE EFFICIENCY IN THE WORKPLACE, WE PROVIDE UNPARALLELED SERVICE IN THE INDUSTRY. DEVELOPING LASTING RELATIONSHIPS WITH OUR CLIENTS AND ASSOCIATES IS THE CORNERSTONE OF OUR SUCCESS.

We'd like to convey the image of a cutting edge, technology based company. Want the cards to pop.

Target Market(s)

Commercial Property Managers - 20 to 50 year old professionals

Industry/Entity Type

Business

Requirements
Must have
• Must utilize our logo obviously, but are definitely open to using variations on the logo. Utilizing the components of the logo, but maybe in different configurations or backgrounds, etc...

Must use the Name: KORVANEX.
Can also use KORVANEX PROPERTY SERVICES.

Must include the Mission Statement

Must say: Where Care Finds Its Pulse
Nice to have
• We are considering plastic stock, shaped cards, or folding cards.

Nothing over the top or really expensive, but will consider if it conveys innovation and technology.
Should not have
• No images of toilets, buildings, trees, or anything relating to commercial properties.

We want to convey our technology image.

```html
<!DOCTYPE html>
<html lang="en">
<head>
<meta charset="utf-8">
<title>KORVANEX – Business Card, Front and Back</title>
<link rel="stylesheet" href="https://fonts.googleapis.com/css2?family=Questrial&family=PT+Sans:wght@400;700&display=swap">
<style>
  :root {
    --navy: #0d4a7b;
    --navy-deep: #0a3f6b;
    --stock: #eef1f3;
    --stock-edge: #d9dee2;
    --silver-light: #f4f5f6;
    --silver-mid: #b9bec3;
    --silver-dark: #7d8389;
    --white: #ffffff;
    --backdrop: #e4e7ea;
  }
  * { box-sizing: border-box; margin: 0; padding: 0; }
  html, body { width: 1200px; height: 900px; overflow: hidden; }
  body {
    background: var(--backdrop);
    font-family: "Questrial", sans-serif;
    position: relative;
  }
  .card {
    position: absolute;
    background: var(--stock);
    border: 1px solid var(--stock-edge);
    border-radius: 18px;
    overflow: hidden;
    box-shadow: 0 6px 18px rgba(0,0,0,.12);
  }
  .card-front { left: 398px; top: 50px; width: 543px; height: 310px; }
  .card-back  { left: 228px; top: 408px; width: 555px; height: 317px; }
  .card-art { position: absolute; inset: 0; width: 100%; height: 100%; }

  /* front */
  .brand {
    position: absolute; left: 22px; top: 100px;
    display: flex; align-items: center; gap: 12px;
    white-space: nowrap;
  }
  .brand-square { width: 40px; height: 40px; background: var(--navy); border-radius: 4px; flex: none; }
  .brand-name {
    color: var(--navy); font-family: "Questrial", sans-serif;
    font-size: 26px; letter-spacing: 1px;
  }
  .tagline {
    position: absolute; right: 18px; top: 22px;
    text-align: right; color: var(--navy);
    font-size: 18px; line-height: 23px;
    white-space: nowrap;
  }
  .holder { position: absolute; left: 34px; top: 248px; color: var(--white); }
  .holder-name { font-size: 18px; line-height: 22px; }
  .holder-role { font-size: 13px; line-height: 18px; opacity: .95; }
  .contacts {
    position: absolute; right: 28px; top: 162px;
    list-style: none; text-align: right; color: var(--white);
    font-size: 14px; letter-spacing: .6px;
  }
  .contacts li {
    height: 27px; display: flex; align-items: center; justify-content: flex-end; gap: 6px;
    white-space: nowrap;
  }
  .contacts svg { width: 11px; height: 11px; fill: var(--white); flex: none; }

  /* back: front design showing through the clear stock, mirrored */
  .show-through {
    position: absolute; inset: 0; transform: scaleX(-1); opacity: .85;
  }
  .show-through .tagline { right: 17px; top: 22px; font-size: 18px; line-height: 24px; }
  .show-through .brand { left: 20px; top: 48px; }
  .mission {
    position: absolute; left: 20px; top: 170px; width: 360px;
    color: var(--white); font-family: "PT Sans", sans-serif;
    font-size: 14.5px; line-height: 18.9px;
  }
  .mission span { display: block; white-space: nowrap; }
</style>
</head>
<body>

  <section class="card card-front" aria-label="Business card front">
    <svg class="card-art" viewBox="0 0 543 310" preserveAspectRatio="none" aria-hidden="true">
      <defs>
        <linearGradient id="silverFront" x1="0" y1="0" x2="1" y2="0">
          <stop offset="0" stop-color="var(--silver-dark)"/>
          <stop offset=".35" stop-color="var(--silver-light)"/>
          <stop offset=".7" stop-color="var(--silver-mid)"/>
          <stop offset="1" stop-color="var(--silver-dark)"/>
        </linearGradient>
      </defs>
      <path d="M0,195 C70,225 150,232 250,180 C350,128 450,92 543,80 L543,92 C450,104 350,140 250,196 C150,252 70,246 0,222 Z" fill="url(#silverFront)"/>
      <path d="M0,222 C70,246 150,252 250,196 C350,140 450,104 543,92 L543,310 L0,310 Z" fill="var(--navy)"/>
    </svg>

    <div class="brand">
      <span class="brand-square"></span>
      <span class="brand-name">KORVANEX</span>
    </div>
    <p class="tagline">Where Care<br>Finds Its Pulse</p>

    <div class="holder">
      <p class="holder-name">Your Name</p>
      <p class="holder-role">Designation</p>
    </div>

    <ul class="contacts">
      <li><svg viewBox="0 0 10 10"><rect x="2.5" y="0" width="5" height="10" rx="1"/></svg>+12 345 67 8910</li>
      <li><svg viewBox="0 0 10 10"><path d="M2,0 L4,0 L4.5,3 L3,4 C3.8,5.6 4.6,6.4 6,7 L7,5.5 L10,6 L10,8 C10,9 9,10 8,10 C3.6,10 0,6.4 0,2 C0,1 1,0 2,0Z"/></svg>+12 345 67 8910a</li>
      <li><svg viewBox="0 0 10 10"><path d="M0,2 L10,2 L10,8 L0,8 Z M0.8,2.6 L5,5.6 L9.2,2.6" fill="none" stroke="#fff" stroke-width="1.2"/></svg>info@yourwebsite.com</li>
      <li><svg viewBox="0 0 10 10"><circle cx="5" cy="5" r="4.5"/></svg>www.yourwebsite.com</li>
      <li><svg viewBox="0 0 10 10"><path d="M5,0 L10,5 L8.5,5 L8.5,10 L6,10 L6,7 L4,7 L4,10 L1.5,10 L1.5,5 L0,5 Z"/></svg>123, Abc Street, 0000 City, Country</li>
    </ul>
  </section>

  <section class="card card-back" aria-label="Business card back">
    <svg class="card-art" viewBox="0 0 555 317" preserveAspectRatio="none" aria-hidden="true">
      <defs>
        <linearGradient id="silverBack" x1="0" y1="0" x2="1" y2="0">
          <stop offset="0" stop-color="var(--silver-dark)"/>
          <stop offset=".4" stop-color="var(--silver-light)"/>
          <stop offset=".75" stop-color="var(--silver-mid)"/>
          <stop offset="1" stop-color="var(--silver-dark)"/>
        </linearGradient>
      </defs>
      <path d="M0,88 C120,92 220,140 320,190 C400,228 480,238 555,228 L555,317 L0,317 Z" fill="var(--navy)"/>
      <path d="M0,84 C120,86 225,130 325,178 C405,214 480,226 555,214 L555,236 C480,246 400,238 320,198 C220,148 120,98 0,94 Z" fill="url(#silverBack)"/>
    </svg>

    <div class="show-through" aria-hidden="true">
      <p class="tagline">Where Care<br>Finds Its Pulse</p>
      <div class="brand">
        <span class="brand-square"></span>
        <span class="brand-name">KORVANEX</span>
      </div>
    </div>

    <p class="mission">
      <span>Korvanex is the leading</span>
      <span>building services innovator. By</span>
      <span>combining technology with functional</span>
      <span>toos that improve efficiency in the workplace,</span>
      <span>we provide unparalleled service in the industry.</span>
      <span>Developing lasting relationships with our clients and</span>
      <span>associates is the cornerstone of our success.</span>
    </p>
  </section>

</body>
</html>
```